Business Card Design Project

you do have a logo of ares but open for anything new . main color is royal blue and white ...are give us some ideas if you like
company name is Merrow's Lawn, Tree and Landscape Contractor
PAVERS
-Pool Decks
-Driveways
-Patios
-Sidewalks & Steps
-Fire Pits
-Retaining Walls
-Layover
-All Patterns and Colors
-To view and/or create your color choice and Patterns visit www.gablestonetiles.com
Custom Concrete Work
-Sea Walls
-Slabs
-Sidewalks
-Concrete Stamping
-Custom Walls
-Custom Curbing
-Concrete Stain (Acid and Eco-Stains available)
-Concrete Sealer
-All Concrete Jobs Call And Ask
-To view and/or create your color choice visit Kemble Tint's Slab Studio app at www.slabstudioapp.com
Pest Control
-Lawns insect, fungus and weed control
-Lawn Fertilization
-Outdoor Pest
- Indoor Pest Control
-Termite Control
-White Fly Treatment
-Rodent Control
IRRIGATION
-installs
-Repair
-Service of Irrigation
Landscape & Installation (residential and commercial)
-Full Lawn Care Service
-Landscape Maintenance
-Weed Control in Flower Beds
-Sod Installation
-Tree Trimming
-Tree Removal
-Bush Pruning
-All Tree & Plant Treatment for Bug, Dieses & Fungus Control
Landscape Material Delivery & Install
-Plants and Tree Install
-Rock, Mulch, Soil, Sand and Riprap
-Weed mat
-Boulders and Flagstone
-Pavers
Call 555.318.4072 for more information.
Residential, Commercial, condos, H.O.A
Lic. & Ins.

```html
<!DOCTYPE html>
<html lang="en">
<head>
<meta charset="utf-8">
<title>Merrow's Lawn – Business Card</title>
<link href="https://fonts.googleapis.com/css2?family=Lobster&family=Open+Sans:wght@400;600;800&display=swap" rel="stylesheet">
<style>
  :root {
    --page-bg: #363330;
    --card-bg: #1b1b1c;
    --card-bg-deep: #121213;
    --panel-bg: #161617;
    --blue-light: #3fb2f0;
    --blue: #1c8fdc;
    --blue-dark: #0d5f9e;
    --accent-blue: #1e8fe0;
    --white: #ffffff;
    --text-soft: #e6e6e6;
  }
  * { margin: 0; padding: 0; box-sizing: border-box; }
  html, body { width: 1200px; height: 2259px; overflow: hidden; background: var(--page-bg); }
  body { font-family: "Open Sans", Arial, sans-serif; position: relative; }

  .card {
    position: absolute;
    left: 89px;
    width: 1022px;
    height: 606px;
    background: radial-gradient(ellipse at 50% 40%, var(--card-bg) 0%, var(--card-bg-deep) 100%);
    border: 2px solid #4a4744;
    overflow: hidden;
  }
  .card--front { top: 463px; }
  .card--back { top: 1189px; }

  .band {
    position: absolute;
    left: 0; right: 0;
    top: 232px;
    height: 162px;
    background: linear-gradient(180deg, var(--blue-light) 0%, var(--blue) 45%, var(--blue-dark) 100%);
    box-shadow: 0 8px 16px rgba(0,0,0,.6);
    display: flex;
    align-items: center;
  }
  .brand-name {
    font-family: "Open Sans", Arial, sans-serif;
    font-weight: 800;
    color: var(--white);
  }
  .card--front .brand-name { font-size: 38px; padding-left: 22px; width: 429px; line-height: 1.15; }
  .card--back .brand-name { font-size: 40px; width: 100%; text-align: center; }

  .contact-panel {
    position: absolute;
    left: 429px;
    top: 0;
    width: 494px;
    height: 560px;
    background: var(--panel-bg);
    box-shadow: 0 0 30px rgba(0,0,0,.85);
  }
  .owner-name {
    font-family: "Lobster", cursive;
    color: var(--white);
    font-size: 72px;
    text-align: center;
    margin-top: 60px;
    line-height: 1;
  }
  .owner-role {
    color: var(--accent-blue);
    text-align: center;
    font-size: 30px;
    letter-spacing: 9px;
    margin-top: 6px;
  }
  .contact-list { list-style: none; position: absolute; left: 0; top: 240px; width: 100%; }
  .contact-row { display: flex; align-items: center; height: 62px; }
  .contact-label {
    width: 140px;
    text-align: right;
    font-size: 34px;
    color: var(--text-soft);
  }
  .contact-icon { width: 40px; height: 40px; margin: 0 14px 0 22px; flex: none; }
  .contact-value { font-size: 23px; color: var(--text-soft); }
</style>
</head>
<body>

<section class="card card--front" aria-label="Business card front">
  <div class="band">
    <span class="brand-name">Merrow's Lawn, Tree and Landscape Contractor</span>
  </div>
  <div class="contact-panel">
    <h1 class="owner-name">Owner name</h1>
    <p class="owner-role">Lorem Ipsum</p>
    <ul class="contact-list">
      <li class="contact-row">
        <span class="contact-label">Phone</span>
        <svg class="contact-icon" viewBox="0 0 24 24" aria-hidden="true"><rect x="7" y="2" width="10" height="20" rx="2" fill="none" stroke="#eee" stroke-width="1.8"/><rect x="9" y="5" width="6" height="7" fill="#eee"/><circle cx="12" cy="17" r="1.5" fill="#eee"/></svg>
        <span class="contact-value">555.318.4072</span>
      </li>
      <li class="contact-row">
        <span class="contact-label">Fax</span>
        <svg class="contact-icon" viewBox="0 0 24 24" aria-hidden="true"><rect x="7" y="2" width="10" height="7" fill="#eee"/><rect x="3" y="9" width="18" height="9" rx="1.5" fill="#eee"/><rect x="7" y="15" width="10" height="7" fill="#eee" stroke="#161617" stroke-width="1.2"/></svg>
        <span class="contact-value">555.318.4073</span>
      </li>
      <li class="contact-row">
        <span class="contact-label">Email</span>
        <svg class="contact-icon" viewBox="0 0 24 24" aria-hidden="true"><rect x="2" y="5" width="20" height="14" fill="#eee"/><path d="M2 5 L12 13 L22 5" fill="none" stroke="#161617" stroke-width="1.6"/></svg>
        <span class="contact-value">office@merrowslawn.com</span>
      </li>
      <li class="contact-row">
        <span class="contact-label">Web</span>
        <svg class="contact-icon" viewBox="0 0 24 24" aria-hidden="true" fill="none" stroke="#eee" stroke-width="1.6"><circle cx="12" cy="12" r="9.5"/><ellipse cx="12" cy="12" rx="4.5" ry="9.5"/><path d="M2.5 12h19M4 7h16M4 17h16"/></svg>
        <span class="contact-value">www.gablestonetiles.com</span>
      </li>
    </ul>
  </div>
</section>

<section class="card card--back" aria-label="Business card back">
  <div class="band">
    <span class="brand-name">Merrow's Lawn, Tree and Landscape Contractor</span>
  </div>
</section>

</body>
</html>
```